Web Design Project

This is a wordpress project for a newly formed biologics company based in the US with international clientele. We do manufacturing of biologically based raw materials using a state of the art facility....Our logo must be incorporated....logo colors Navy and Gray. It is fine to use some color in web design. The viewer will primarily be industry folk.

Torvell Biologics, LLC is a contract manufacturing organization which produces biologically-based raw materials derived primarily from human plasma. The company services include extraction and purification of plasma components, especially proteins and enzymes. The business focuses on biotherapeutics, diagnostic and veterinary markets worldwide.

5 pages a bad example of first page can be found in attached files.....
use stock photos of labs and clean rooms.
Updates

Project Deadline Extended
Reason: I need a bit more time tonprovide feedback.

Project Deadline Extended
Reason: needed time to evaluate existing options

Target Market(s)

target market Pharmaceutical companies and research universities

Industry/Entity Type

Veterinary

Requirements
Must have
• our logo...we will provide some graphics...

```html
<!DOCTYPE html>
<html lang="en">
<head>
<meta charset="utf-8">
<title>Torvell Biologics, LLC</title>
<link href="https://fonts.googleapis.com/css2?family=PT+Sans:wght@400;700&family=Open+Sans:wght@400&family=Arimo:wght@400;700&display=swap" rel="stylesheet">
<style>
:root{
  --navy:#1d4a85;
  --navy-dark:#163a6a;
  --nav-top:#3f6aa3;
  --nav-bottom:#1c4478;
  --red:#c8200e;
  --heading-gray:#5d5d5d;
  --subtitle-gray:#8c8c8c;
  --body-text:#555555;
  --maroon:#5a1a1c;
  --header-bg:#f8f8f8;
  --sidebar-bg:#efefef;
  --strip:#d2d2d2;
  --rule:#dcdcdc;
}
*{box-sizing:border-box;margin:0;padding:0}
html,body{width:1059px;height:1200px;overflow:hidden;background:#fff}
.page{position:absolute;left:0;top:0;width:1000px;height:1133px;transform:scale(1.059);transform-origin:0 0;font-family:"Arimo",Arial,sans-serif;color:var(--body-text)}
.abs{position:absolute}
.top-bar{left:0;top:0;width:1000px;height:10px;background:var(--navy)}
.site-header{left:0;top:10px;width:1000px;height:105px;background:var(--header-bg)}
.brand{left:20px;top:4px;display:flex;align-items:center;gap:10px}
.brand-mark{width:95px;height:95px;border-radius:50%;background:var(--navy)}
.brand-name{font-family:"Arimo",Arial,sans-serif;font-weight:700;font-size:34px;color:var(--navy);letter-spacing:-.5px}
.hero{left:0;top:115px;width:1000px;height:363px;background:linear-gradient(90deg,#0d4f8c 0%,#2f7fc0 18%,#c24a08 32%,#f08a12 48%,#ffb000 58%,#e87410 70%,#f0a030 85%,#e2e2e2 100%)}
.slider-dots{left:925px;top:449px;width:52px;height:20px;background:rgba(20,20,20,.75);border-radius:2px;display:flex;justify-content:center;align-items:center;gap:6px}
.slider-dots span{width:8px;height:8px;border-radius:50%;background:#888}
.slider-dots span.active{background:#2d84e0}
.main-nav{left:0;top:478px;width:1000px;height:50px;background:linear-gradient(180deg,var(--nav-top),var(--nav-bottom))}
.nav-item{top:0;height:50px;line-height:50px;width:116px;text-align:center;color:#fff;font-family:"Open Sans",sans-serif;font-size:15px}
.nav-sep{top:6px;width:1px;height:38px;background:rgba(10,30,60,.6)}
.search{left:753px;top:490px;width:218px;height:28px;background:var(--navy-dark);border:1px solid #4d79b3;color:#d8e2ef;font-family:"Open Sans",sans-serif;font-size:12px;line-height:26px;padding-left:12px}
.search svg{position:absolute;right:10px;top:5px}
.strip{left:0;top:528px;width:1000px;height:14px;background:var(--strip)}
.sidebar{left:697px;top:542px;width:278px;height:517px;background:var(--sidebar-bg)}
.title{font-family:"PT Sans",sans-serif;font-weight:700;font-size:19px;color:var(--heading-gray);text-transform:uppercase}
.title em{font-style:normal;color:var(--red)}
.welcome{left:27px;top:570px;font-family:"PT Sans",sans-serif;font-weight:700;font-size:27px;color:var(--red);line-height:30px}
.welcome-sub{left:27px;top:598px;font-family:"PT Sans",sans-serif;font-weight:700;font-size:17px;color:var(--subtitle-gray);white-space:pre}
.copy{font-size:12.4px;line-height:18px;color:var(--body-text)}
.btn{height:29px;background:var(--maroon);color:#fff;font-size:13px;text-align:center;line-height:29px;text-transform:uppercase}
.rule{height:1px;background:var(--rule)}
.service-list{left:32px;top:860px;list-style:none}
.service-list li{height:25px;font-size:12.4px;color:var(--body-text);display:flex;align-items:center;gap:9px}
.service-list li::before{content:"";border-left:6px solid #555;border-top:4px solid transparent;border-bottom:4px solid transparent}
.news-date{font-size:12px;font-weight:700;color:#222}
.staff{left:712px;top:918px;width:250px;height:120px;background:linear-gradient(90deg,#f4f4f4 0%,#eaeaea 45%,#d9c9a8 62%,#e6e2dc 80%,#cfcfcf 100%)}
.staff-label{left:726px;top:926px;font-family:"PT Sans",sans-serif;font-weight:700;font-size:29px;line-height:28px;color:var(--red)}
.footer{left:0;top:1059px;width:1000px;height:74px;background:linear-gradient(180deg,#2a5a98,#1e4a85 60%,#3d6aa5)}
.footer-links{left:0;top:1077px;width:1000px;text-align:center;color:#fff;font-family:"Open Sans",sans-serif;font-size:12px;line-height:20px}
.social{top:1086px;width:22px;height:22px;border-radius:2px}
</style>
</head>
<body>
<div class="page">
  <div class="abs top-bar"></div>
  <header class="abs site-header">
    <div class="abs brand"><span class="brand-mark"></span><span class="brand-name">Torvell Biologics</span></div>
  </header>

  <div class="abs hero" role="img" aria-label="Close-up photo of laboratory flasks with orange and blue liquids"></div>
  <div class="abs slider-dots"><span class="active"></span><span></span><span></span></div>

  <nav class="abs main-nav">
    <a class="abs nav-item" style="left:36px">Home</a>
    <span class="abs nav-sep" style="left:152px"></span>
    <a class="abs nav-item" style="left:152px">Laboratory</a>
    <span class="abs nav-sep" style="left:268px"></span>
    <a class="abs nav-item" style="left:270px">Research</a>
    <span class="abs nav-sep" style="left:384px"></span>
    <a class="abs nav-item" style="left:383px">Team</a>
    <span class="abs nav-sep" style="left:500px"></span>
    <a class="abs nav-item" style="left:499px">Press</a>
    <span class="abs nav-sep" style="left:616px"></span>
    <a class="abs nav-item" style="left:614px">Contact us</a>
    <span class="abs nav-sep" style="left:732px"></span>
  </nav>
  <div class="abs search">Search
    <svg width="16" height="16" viewBox="0 0 16 16"><circle cx="6.5" cy="6.5" r="4.8" fill="none" stroke="#fff" stroke-width="1.6"/><line x1="10" y1="10" x2="15" y2="15" stroke="#fff" stroke-width="2"/></svg>
  </div>
  <div class="abs strip"></div>

  <div class="abs sidebar"></div>

  <h1 class="abs welcome">WELCOME</h1>
  <h2 class="abs welcome-sub">TO OUR  TORVELL BIOLOGICS, LLC</h2>
  <p class="abs copy" style="left:29px;top:635px;width:636px">Pellentesque suscipit dictum eleifend. Ut urna diam, iaculis faucibus fringilla non, tincidunt ut dolor. Nulla ullamcorper porttitor tellus, in volutpat velit interdum id. Aliquam erat volutpat. Maecenas vel nulla nibh, sed accumsan ante. Mauris nec urna massa, a blandit nulla. Sed felis odio, tempus non dapibus vitae, placerat nec augue. Etiam molestie ligula eu odio commodo tempus. Phasellus ullamcorper libero sed felis tempor eu ullamcorper orci egestas. Etiam tempor mollis risus vel dapibus. Donec id nisl sed lectus ullamcorper pellentesque. Sed quis mi nisi. Integer volutpat tincidunt libero.</p>
  <a class="abs btn" style="left:539px;top:744px;width:119px">Read more</a>
  <div class="abs rule" style="left:33px;top:791px;width:633px"></div>

  <h3 class="abs title" style="left:27px;top:818px"><em>Featured</em> services</h3>
  <ul class="abs service-list">
    <li>Etiam a odio et odio euismod placerat</li>
    <li>Maecenas adipiscing leo non turpis</li>
    <li>Praesent nec sem massa, et</li>
    <li>Nam tempus viverra magna, at volutpat</li>
    <li>Etiam a odio et odio euismod</li>
  </ul>
  <a class="abs btn" style="left:152px;top:997px;width:119px">Read more</a>
  <div class="abs" style="left:306px;top:813px;width:1px;height:177px;background:var(--rule)"></div>

  <h3 class="abs title" style="left:338px;top:818px"><em>What</em> we do</h3>
  <p class="abs copy" style="left:338px;top:856px;width:316px">Etiam molestie ligula eu odio commodo tempus. Phasellus ullamcorper libero sed felis tempor eu ullamcorper orci egestas. Etiam tempor mollis risus vel dapibus. Donec id nisl sed lectus ullamcorper pellentesque. Sed quis mi nisi. Integer volutpat tincidunt libero. Etiam tempor mollis risus vel dapibus. Donec id nisl sed lectus ullamcorper pellentes-que. Sed quis mi nisi. Integer volutpat tincidunt libero.</p>
  <a class="abs btn" style="left:539px;top:997px;width:119px">Read more</a>

  <h3 class="abs title" style="left:717px;top:577px"><em>Latest</em> news</h3>
  <p class="abs news-date" style="left:717px;top:629px">10 feb 2012</p>
  <p class="abs copy" style="left:717px;top:651px;width:245px">Etiam tempor mollis risus vel dapibus. Donec id nisl sed lectus ullamcorper pellentesque. Sed quis mi nisi.</p>
  <a class="abs btn" style="left:857px;top:716px;width:99px;height:24px;line-height:24px">Read more</a>
  <div class="abs rule" style="left:709px;top:757px;width:254px;background:#cfcfcf"></div>
  <p class="abs news-date" style="left:717px;top:776px">10 feb 2012</p>
  <p class="abs copy" style="left:717px;top:798px;width:245px">Etiam tempor mollis risus vel dapibus. Donec id nisl sed lectus ullamcorper pellentesque. Sed quis mi nisi.</p>
  <a class="abs btn" style="left:857px;top:863px;width:99px;height:24px;line-height:24px">Read more</a>

  <div class="abs staff" role="img" aria-label="Photo of a laboratory staff member beside a microscope"></div>
  <p class="abs staff-label">Our<br>Staff</p>
  <svg class="abs" style="left:737px;top:990px" width="28" height="28" viewBox="0 0 28 28"><circle cx="14" cy="14" r="12" fill="#e8e8e8" stroke="#555" stroke-width="2"/><path d="M9 9 L19 14 L9 19 L12 14 Z" fill="#555"/></svg>

  <footer class="abs footer"></footer>
  <div class="abs footer-links">Home | Laboratory | Research | Team | Press | Contact us<br>2012 © copyrights.torvellbiologics.received</div>
  <span class="abs social" style="left:830px;background:#4a63a0"></span>
  <span class="abs social" style="left:860px;background:#5cb6e4"></span>
  <span class="abs social" style="left:890px;background:#e8742a"></span>
  <span class="abs social" style="left:920px;background:#1b7ab8"></span>
  <span class="abs social" style="left:950px;background:#d8d8d8"></span>
</div>
</body>
</html>
```